KRT Flyer to attract applicants 11x17

Lantern Stagehand Collective provides crew for local concerts, filming, theater, and corporate events.
The flyer will be posted on bulletin boards at colleges with theater programs.
Our primary venues are historic theaters in downtown LA
Need a 11x17 poster to attract potential applicants/crew
I have attached a poster that one of our staff made that has all if the relevant info - but i know the poster can look much better than that. I have also attached many images and our logo. It is not necessary to use all of the images, or any of them. The two images of the theater interiors are the venues we operate so they would be the first to include. I can send additional info or images upon request. Thank you

Industry/Entity Type

Entertainment

Requirements
Must have
• APPLY@KRTCREW.EXAMPLE

```html
<!DOCTYPE html>
<html lang="en">
<head>
<meta charset="utf-8">
<title>KRT Crew Recruitment Flyer</title>
<link rel="stylesheet" href="https://fonts.googleapis.com/css2?family=Poppins:wght@300;400;700;800&family=Oswald:wght@500&display=swap">
<style>
  :root {
    --backdrop: #e9ebee;
    --blue-deep: #1a4f9c;
    --blue-mid: #1f6fbf;
    --blue-bright: #2a8fd6;
    --teal: #1aa6a6;
    --teal-light: #24c0b4;
    --white: #ffffff;
    --ink-soft: #dce9f7;
    --theater-warm: #7a2a1a;
    --theater-gold: #c7782c;
    --stage-violet: #5a2d86;
    --night-navy: #0f1f45;
    --console-amber: #b48a4a;
  }
  * { margin: 0; padding: 0; box-sizing: border-box; }
  html, body { width: 1200px; height: 1200px; overflow: hidden; background: var(--backdrop); }
  .canvas { position: relative; width: 1200px; height: 1200px; }
  .flyer {
    position: absolute; left: 210px; top: 40px; width: 780px; height: 1120px;
    overflow: hidden; background: linear-gradient(160deg, var(--blue-bright) 0%, var(--blue-mid) 55%, var(--blue-deep) 100%);
    box-shadow: 0 18px 40px rgba(0,0,0,0.18);
  }
  .flyer-art { position: absolute; inset: 0; width: 780px; height: 1120px; }
  .brand-badge {
    position: absolute; left: 60px; top: 560px; width: 190px; height: 190px; border-radius: 50%;
    background: #e6e7ea; display: flex; align-items: center; justify-content: center; text-align: center;
    font-family: "Poppins", sans-serif; font-weight: 700; font-size: 19px; line-height: 1.2;
    color: var(--blue-deep); padding: 26px; text-transform: uppercase;
  }
  .headline {
    position: absolute; left: 60px; top: 780px; font-family: "Poppins", sans-serif; font-weight: 800;
    font-size: 82px; line-height: 0.98; color: var(--white); letter-spacing: 1px; text-transform: uppercase;
  }
  .intro {
    position: absolute; left: 62px; top: 960px; width: 360px; font-family: "Poppins", sans-serif;
    font-weight: 300; font-size: 19px; line-height: 1.3; color: var(--ink-soft);
  }
  .apply-band {
    position: absolute; left: 0; top: 1040px; width: 780px; height: 52px;
    background: linear-gradient(90deg, var(--teal-light), var(--teal) 60%, var(--blue-mid));
    display: flex; align-items: center; padding-left: 60px;
    font-family: "Oswald", sans-serif; font-weight: 500; font-size: 30px; color: var(--white); letter-spacing: 0.5px;
  }
  .website {
    position: absolute; left: 0; top: 1092px; width: 780px; height: 28px; background: var(--blue-deep);
    padding-left: 270px; font-family: "Poppins", sans-serif; font-weight: 700; font-size: 15px;
    line-height: 28px; color: var(--white);
  }
</style>
</head>
<body>
<div class="canvas">
  <section class="flyer">
    <svg class="flyer-art" viewBox="0 0 780 1120" xmlns="http://www.w3.org/2000/svg">
      <defs>
        <linearGradient id="theaterTone" x1="0" y1="0" x2="1" y2="1">
          <stop offset="0" stop-color="var(--theater-warm)"/>
          <stop offset="0.5" stop-color="var(--theater-gold)"/>
          <stop offset="1" stop-color="var(--stage-violet)"/>
        </linearGradient>
        <linearGradient id="performerTone" x1="0" y1="0" x2="1" y2="1">
          <stop offset="0" stop-color="#eef2f8"/>
          <stop offset="1" stop-color="#6c7687"/>
        </linearGradient>
        <linearGradient id="skylineTone" x1="0" y1="0" x2="0" y2="1">
          <stop offset="0" stop-color="#23407a"/>
          <stop offset="1" stop-color="var(--night-navy)"/>
        </linearGradient>
        <linearGradient id="consoleTone" x1="0" y1="0" x2="1" y2="1">
          <stop offset="0" stop-color="var(--console-amber)"/>
          <stop offset="1" stop-color="#3b4a5e"/>
        </linearGradient>
        <linearGradient id="accentBand" x1="0" y1="0" x2="1" y2="0">
          <stop offset="0" stop-color="#3aa3e6"/>
          <stop offset="1" stop-color="#1f6fbf"/>
        </linearGradient>
      </defs>

      <polygon points="0,0 470,0 300,440 0,300" fill="url(#theaterTone)" role="img" aria-label="Photo of a historic theater interior with ornate stage and warm lighting"/>
      <polygon points="470,0 490,0 320,440 300,440" fill="url(#accentBand)"/>
      <polygon points="490,0 780,0 780,470 320,470 320,440" fill="var(--white)"/>

      <rect x="540" y="-30" width="200" height="210" rx="26" fill="url(#performerTone)" role="img" aria-label="Photo of a singer performing on a lit stage"/>
      <rect x="380" y="215" width="220" height="230" rx="26" fill="url(#skylineTone)" role="img" aria-label="Photo of a downtown city skyline at night"/>
      <rect x="622" y="215" width="200" height="230" rx="26" fill="url(#consoleTone)" role="img" aria-label="Photo of a sound mixing console"/>
    </svg>

    <div class="brand-badge">Lantern Stagehand Collective</div>
    <h1 class="headline">Has Open<br>Positions</h1>
    <p class="intro">We are looking for talented technicians to add to our roster of skilled professionals.</p>
    <div class="apply-band">SEND RESUME TO : APPLY@KRTCREW.EXAMPLE</div>
    <div class="website">www.krtcrew.example</div>
  </section>
</div>
</body>
</html>
```